Professional Photography Business cards

I need business cards that include my logo which I have uploaded. I run a photography business. I am open to ideas but I would like one side to have my logo and the other side to have my contact info. I don't have a website made but I do own a website domain. I have uploaded 2 different logo color schemes. My business colors are Blue, black , and white.

Business Name
Business Phone Number
Business Email
Business Website address
Instagram

Industry/Entity Type

Professional Photography

Contact Information for Business Card

Phone Number: 916-384-7702 email: info@tlane-studio.example Instagram: @t.lanestudio website doman- www.tlane-studio.example

Requirements
Must have
• I like the idea of a business card with a full black background front and back of card. My colors must include royal blue, black, and white

```html
<!DOCTYPE html>
<html lang="en">
<head>
<meta charset="utf-8">
<title>T. Lane Studio — Business Cards</title>
<link href="https://fonts.googleapis.com/css2?family=Montserrat:wght@400;500&display=swap" rel="stylesheet">
<style>
  :root {
    --backdrop: #1c1c1e;
    --card-black: #0b0b0c;
    --royal-blue: #1a22c4;
    --white: #ffffff;
    --soft-grey: #8a8a8e;
  }
  * { margin: 0; padding: 0; box-sizing: border-box; }
  html, body {
    width: 1200px;
    height: 1015px;
    overflow: hidden;
    background: var(--backdrop);
    font-family: "Montserrat", Arial, sans-serif;
  }
  .sheet {
    position: relative;
    width: 1200px;
    height: 1015px;
  }
  .card {
    position: absolute;
    left: 300px;
    width: 600px;
    height: 343px;
    background: var(--card-black);
    border-bottom: 6px solid var(--royal-blue);
    box-shadow: 0 0 0 1px var(--royal-blue), 0 18px 40px rgba(0,0,0,.6);
  }
  .card--front { top: 110px; }
  .card--back { top: 552px; }

  .brand-name {
    font-weight: 500;
    letter-spacing: 0.06em;
    white-space: nowrap;
  }
  .card--front .brand {
    position: absolute;
    inset: 0;
    display: flex;
    align-items: center;
    justify-content: center;
    gap: 14px;
  }
  .card--front .brand-name {
    font-size: 34px;
    color: var(--soft-grey);
  }
  .brand-dot {
    width: 18px;
    height: 18px;
    border-radius: 50%;
    border: 2px solid var(--soft-grey);
  }

  .card--back .brand {
    position: absolute;
    left: 150px;
    top: 62px;
    display: flex;
    align-items: center;
    gap: 12px;
  }
  .card--back .brand-name {
    font-size: 30px;
    color: var(--white);
  }
  .card--back .brand-dot { border-color: var(--white); }

  .contact-list {
    position: absolute;
    left: 190px;
    top: 158px;
    list-style: none;
    color: var(--white);
    font-size: 17px;
    font-weight: 400;
  }
  .contact-item {
    display: flex;
    align-items: center;
    gap: 12px;
    height: 30px;
  }
  .contact-item--social { margin-top: 14px; }
  .contact-icon {
    width: 18px;
    height: 18px;
    flex: none;
  }
  .contact-icon--square {
    width: 16px;
    height: 16px;
    border: 2px solid var(--royal-blue);
    border-radius: 3px;
  }
</style>
</head>
<body>
<main class="sheet">
  <section class="card card--front" aria-label="Card front">
    <div class="brand">
      <span class="brand-dot"></span>
      <span class="brand-name">T. Lane Studio</span>
    </div>
  </section>

  <section class="card card--back" aria-label="Card back">
    <div class="brand">
      <span class="brand-dot"></span>
      <span class="brand-name">T. Lane Studio</span>
    </div>
    <ul class="contact-list">
      <li class="contact-item">
        <svg class="contact-icon" viewBox="0 0 24 24" aria-hidden="true">
          <path fill="var(--royal-blue)" d="M6.6 10.8a15 15 0 0 0 6.6 6.6l2.2-2.2a1 1 0 0 1 1-.25 11.4 11.4 0 0 0 3.6.57 1 1 0 0 1 1 1V20a1 1 0 0 1-1 1A17 17 0 0 1 3 4a1 1 0 0 1 1-1h3.5a1 1 0 0 1 1 1c0 1.25.2 2.45.57 3.57a1 1 0 0 1-.25 1z"/>
        </svg>
        <span>916-384-7702</span>
      </li>
      <li class="contact-item">
        <svg class="contact-icon" viewBox="0 0 24 24" aria-hidden="true">
          <rect x="2" y="5" width="20" height="14" rx="1.5" fill="var(--royal-blue)"/>
          <path d="M3 6l9 7 9-7" fill="none" stroke="var(--card-black)" stroke-width="1.6"/>
        </svg>
        <span>info@tlane-studio.example</span>
      </li>
      <li class="contact-item">
        <svg class="contact-icon" viewBox="0 0 24 24" aria-hidden="true">
          <g fill="none" stroke="var(--royal-blue)" stroke-width="1.8">
            <circle cx="12" cy="12" r="9.5"/>
            <ellipse cx="12" cy="12" rx="4" ry="9.5"/>
            <path d="M2.5 12h19M4 7h16M4 17h16"/>
          </g>
        </svg>
        <span>www.tlane-studio.example</span>
      </li>
      <li class="contact-item contact-item--social">
        <span class="contact-icon contact-icon--square"></span>
        <span>@t.lanestudio</span>
      </li>
    </ul>
  </section>
</main>
</body>
</html>
```